Business Card and Simple Logo Desgin

New Zealand based start up company "Vesta Advisory LTD" requires business cards and simple logo design.

Card Content.

Vesta Advisory LTD

Rebecca Thornbury
CA, BMS (Hons)

r.thornbury@vestaadvisory.co.nz
PH +64 21 574 613

Target Market(s)

Corporate Business in IT, Finance and accounting.

Industry/Entity Type

Business

```html
<!DOCTYPE html>
<html lang="en">
<head>
<meta charset="utf-8">
<title>Vesta Advisory LTD – Business Card</title>
<link rel="stylesheet" href="https://fonts.googleapis.com/css2?family=Questrial&display=swap">
<style>
  :root {
    --page-bg: #ece7df;
    --card-top: #1e201f;
    --card-bottom: #4b4341;
    --panel-light: #5b514d;
    --panel-mid: #3a3533;
    --text-light: #dcd8d4;
    --text-soft: #bdb7b2;
    --accent: #e3120b;
    --rule: #d6d2ce;
  }
  * { margin: 0; padding: 0; box-sizing: border-box; }
  html, body {
    width: 1200px;
    height: 900px;
    overflow: hidden;
    background: var(--page-bg);
    font-family: "Questrial", "Century Gothic", sans-serif;
  }
  .canvas { position: relative; width: 1200px; height: 900px; }

  .card {
    position: absolute;
    overflow: hidden;
    background: linear-gradient(to bottom, var(--card-top), var(--card-bottom));
    box-shadow: 0 4px 10px rgba(0, 0, 0, 0.28);
  }
  .card--front { left: 289px; top: 64px; width: 598px; height: 364px; }
  .card--back  { left: 289px; top: 449px; width: 588px; height: 360px; }

  .wordmark {
    position: absolute;
    display: flex;
    align-items: center;
    color: var(--text-light);
    white-space: nowrap;
    letter-spacing: 0.2px;
  }
  .wordmark__dot { background: var(--accent); flex: none; }
  .card--front .wordmark {
    left: 0; right: 0; top: 160px;
    justify-content: center;
    font-size: 27px;
    gap: 10px;
  }
  .card--front .wordmark__dot { width: 12px; height: 12px; }
  .card--back .wordmark {
    left: 14px; top: 15px;
    font-size: 17px;
    gap: 7px;
  }
  .card--back .wordmark__dot { width: 8px; height: 8px; }

  .swoosh { position: absolute; left: 0; top: 0; width: 588px; height: 360px; }

  .contact {
    position: absolute;
    right: 48px;
    text-align: right;
    padding-right: 13px;
  }
  .contact::after {
    content: "";
    position: absolute;
    right: 0; top: 0; bottom: 0;
    width: 3px;
    background: var(--rule);
  }
  .contact--name { top: 246px; height: 35px; }
  .contact--reach { top: 293px; height: 34px; }
  .contact__name, .contact__title {
    font-size: 15.5px;
    line-height: 17.5px;
    color: var(--text-light);
  }
  .contact__line {
    font-size: 13px;
    line-height: 17px;
    color: var(--text-soft);
  }
</style>
</head>
<body>
<main class="canvas">

  <section class="card card--front" aria-label="Card front">
    <div class="wordmark">
      <span class="wordmark__dot"></span>
      <span class="wordmark__name">Vesta Advisory LTD</span>
    </div>
  </section>

  <section class="card card--back" aria-label="Card back">
    <svg class="swoosh" viewBox="0 0 588 360" aria-hidden="true">
      <defs>
        <radialGradient id="panelGlow" cx="110" cy="70" r="260" gradientUnits="userSpaceOnUse">
          <stop offset="0" stop-color="#625854"/>
          <stop offset="0.55" stop-color="#4a4341"/>
          <stop offset="1" stop-color="#2c2a29"/>
        </radialGradient>
        <linearGradient id="edgeShine" x1="0" y1="0" x2="1" y2="0">
          <stop offset="0" stop-color="#7a6e69" stop-opacity="0.5"/>
          <stop offset="1" stop-color="#7a6e69" stop-opacity="0"/>
        </linearGradient>
      </defs>
      <path d="M0,0 H588 C 400,6 240,38 140,125 C 80,178 35,215 0,245 Z" fill="url(#panelGlow)"/>
      <path d="M0,245 C 35,215 80,178 140,125 C 240,38 400,6 588,0"
            fill="none" stroke="url(#edgeShine)" stroke-width="2"/>
    </svg>

    <div class="wordmark">
      <span class="wordmark__dot"></span>
      <span class="wordmark__name">Vesta Advisory LTD</span>
    </div>

    <div class="contact contact--name">
      <p class="contact__name">Rebecca Thornbury</p>
      <p class="contact__title">CA, BMS (Hons)</p>
    </div>
    <div class="contact contact--reach">
      <p class="contact__line">r.thornbury@vestaadvisory.co.nz</p>
      <p class="contact__line">PH +64 21 574 613</p>
    </div>
  </section>

</main>
</body>
</html>
```